We need a business card for our gym. We are a PowerCore affiliate in Decatur Georgie established 2008. Our company name is Rally Functional Fitness. PowerCore Building Prime Fitness. Instagram and website is @rallygym. Hashtags we use #rallywithheart #madetorally We want something similar to the the black and neon green design attached but a different color scheme. No neon colors. Are company colors are the same as the blue and white card attached. We are open to ideas as far as colors however - just no neon.

Contact Information for Business Card

Rally Functional Fitness
472 Halvern Drive
Decatur GA 30041
Phone 404.555.0187 Website www.rallygym.example

Font styles to use
Other font styles liked:
• Futura Extra Bold Condensed

Colors

Designer to choose colors to be used in the design.

Requirements
Must have
• Our primary font we typically use for our name is Futura Extra Bold Condensed
Nice to have
• I attached a card from that is black and neon green from Zorva that we would like something similar. The blue and white is more similar to our colors. We also use have used black and white in the past. We use the chevrons as out logo. We are a PowerCore affiliate so I included a logo from them as well that may or may not be used on the card. Our instagram is @rallygym hashtags #madetorally #rallywithheart
Should not have
• No neon colors

```html
<!DOCTYPE html>
<html lang="en">
<head>
<meta charset="utf-8">
<title>Rally Functional Fitness – Business Card</title>
<link rel="stylesheet" href="https://fonts.googleapis.com/css2?family=Oswald:wght@500;700&family=Montserrat:wght@400;500&display=swap">
<style>
  :root {
    --backdrop: #2b2b2d;
    --card: #242425;
    --card-edge: #303032;
    --accent-blue: #8fd3f5;
    --logo-white: #e9e9ea;
    --divider: #8fd3f5;
  }
  * { box-sizing: border-box; margin: 0; padding: 0; }
  html, body {
    width: 1200px;
    height: 901px;
    overflow: hidden;
    background: var(--backdrop);
  }
  .stage {
    width: 1200px;
    height: 901px;
    display: flex;
    align-items: center;
    justify-content: center;
    gap: 40px;
  }
  .card {
    position: relative;
    width: 540px;
    height: 309px;
    background: var(--card);
    border: 1px solid var(--card-edge);
    overflow: hidden;
  }

  /* Front */
  .card-front {
    display: flex;
    align-items: center;
    justify-content: center;
  }
  .brand-name {
    font-family: "Oswald", sans-serif;
    font-weight: 700;
    font-size: 40px;
    letter-spacing: 1px;
    text-transform: uppercase;
    color: var(--logo-white);
    line-height: 1;
  }

  /* Back */
  .card-back { color: var(--accent-blue); }
  .identity-row {
    position: absolute;
    top: 92px;
    left: 0;
    right: 0;
    display: flex;
    justify-content: center;
    align-items: center;
    gap: 22px;
  }
  .person {
    text-align: right;
  }
  .person-name {
    font-family: "Oswald", sans-serif;
    font-weight: 500;
    font-size: 32px;
    letter-spacing: 0.5px;
    text-transform: uppercase;
    line-height: 1.05;
  }
  .person-role {
    font-family: "Montserrat", sans-serif;
    font-weight: 400;
    font-size: 15px;
    letter-spacing: 0.5px;
    text-transform: uppercase;
    margin-top: 2px;
  }
  .divider {
    width: 1px;
    height: 62px;
    background: var(--divider);
  }
  .contact-list {
    list-style: none;
    font-family: "Montserrat", sans-serif;
    font-weight: 500;
    font-size: 15px;
    line-height: 1.45;
  }
  .contact-list li {
    display: flex;
    align-items: center;
    gap: 8px;
  }
  .contact-list svg {
    width: 13px;
    height: 13px;
    fill: var(--accent-blue);
    flex: none;
  }
  .address {
    position: absolute;
    left: 0;
    right: 0;
    bottom: 34px;
    text-align: center;
    font-family: "Montserrat", sans-serif;
    font-weight: 500;
    font-size: 16px;
    letter-spacing: 0.3px;
  }
  .accent-band {
    position: absolute;
    left: 0;
    right: 0;
    bottom: 0;
    height: 10px;
    background: var(--accent-blue);
  }
</style>
</head>
<body>
<main class="stage">
  <section class="card card-front">
    <p class="brand-name">Rally Functional Fitness</p>
  </section>

  <section class="card card-back">
    <div class="identity-row">
      <div class="person">
        <p class="person-name">Marcus Delaney</p>
        <p class="person-role">Expert Coaches</p>
      </div>
      <div class="divider"></div>
      <ul class="contact-list">
        <li>
          <svg viewBox="0 0 16 16" aria-hidden="true"><path d="M3.5 1.5l2.5 0 1.2 3.3-1.7 1.2a9 9 0 0 0 4.5 4.5l1.2-1.7 3.3 1.2v2.5a1.5 1.5 0 0 1-1.6 1.5A13 13 0 0 1 2 3.1 1.5 1.5 0 0 1 3.5 1.5z"/></svg>
          404.555.0187
        </li>
        <li>
          <svg viewBox="0 0 16 16" aria-hidden="true"><path d="M1 3h14v1.2L8 8.6 1 4.2z"/><path d="M1 5.6l7 4.4 7-4.4V13H1z"/></svg>
          info@rallygym.example
        </li>
        <li>
          <svg viewBox="0 0 16 16" aria-hidden="true"><path d="M8 1a7 7 0 1 0 0 14A7 7 0 0 0 8 1zm0 2a5 5 0 0 1 0 10A5 5 0 0 1 8 3z"/><circle cx="8" cy="8" r="2.4"/></svg>
          www.rallygym.example
        </li>
      </ul>
    </div>
    <p class="address">472 Halvern Drive, Decatur GA 30041</p>
    <div class="accent-band"></div>
  </section>
</main>
</body>
</html>
```